KAJU Freightways #ALLKAJU Business Cards & Letterhead

I am looking to business cards designed for our organization. We are currently undergoing a small re-branding that is taking place. Our organization is called KAJU Freightways and we are headquartered in Phoenix, AZ. We primarily provide transportation and logistics services to the Marlow Parcel Bureau who is our largest customer. I would like to see a design that incorporates name, title, contact info, website, and address (this will be different depending on the employee). I would also like to see some color on the business card using our logo colors or a variation. I would like our logo on the back of the business card with the website displayed. The final design should communicate that we are a next generation transportation operate that focuses on being driver-first, customer-centric, innovative, and sustainable.We would also like our #ALLKAJU catch phrase incorporated as well.

Target Market(s)

Transportation & Logistics

Industry/Entity Type

Trucking Company

Contact Information for Business Card

-First and Last Name
-Position Title
-Contact Phone
-Contact Email
-Physical Address

Font styles to use
Serif

Colors

Designer to choose colors to be used in the design.

Requirements
Must have
• -KAJU logo prominently displayed
• -#ALLKAJU catch phrase used
• -Some amount of color, design gradient, etc.
• -Logo on the back with website listed (https://www.kajufreightco.example)

```html
<!DOCTYPE html>
<html lang="en">
<head>
<meta charset="UTF-8">
<title>KAJU Freightways Business Card</title>
<link href="https://fonts.googleapis.com/css2?family=Lato:wght@400;700;900&display=swap" rel="stylesheet">
<style>
  :root {
    --backdrop: #3b3b3d;
    --brand-green: #7dc242;
    --brand-teal: #0f3f4a;
    --ink: #1f1f1f;
    --paper: #ffffff;
  }
  html, body {
    margin: 0;
    padding: 0;
    width: 1200px;
    height: 1200px;
    overflow: hidden;
    background: var(--backdrop);
    font-family: "Lato", sans-serif;
  }
  .sheet {
    width: 1200px;
    height: 1200px;
    display: flex;
    flex-direction: column;
    align-items: center;
    justify-content: center;
    gap: 44px;
  }
  .card {
    width: 720px;
    height: 410px;
    position: relative;
    box-sizing: border-box;
    box-shadow: 0 10px 24px rgba(0,0,0,0.35);
  }
  /* Front */
  .card--front {
    background: var(--brand-green);
    border-radius: 80px 0 80px 0;
    display: flex;
    flex-direction: column;
    align-items: center;
    justify-content: center;
    color: var(--paper);
  }
  .wordmark {
    display: flex;
    align-items: center;
    gap: 16px;
    font-weight: 900;
    letter-spacing: 2px;
  }
  .wordmark__dot {
    border-radius: 50%;
    display: inline-block;
  }
  .card--front .wordmark { font-size: 78px; color: var(--paper); }
  .card--front .wordmark__dot { width: 26px; height: 26px; background: var(--paper); }
  .front-url {
    position: absolute;
    bottom: 46px;
    left: 0;
    right: 0;
    text-align: center;
    font-weight: 700;
    font-size: 15px;
    letter-spacing: 2px;
  }
  /* Back */
  .card--back {
    background: var(--paper);
    border-radius: 0 80px 0 80px;
    padding: 48px 46px;
    color: var(--ink);
  }
  .person__name {
    margin: 0;
    font-weight: 900;
    font-size: 24px;
    color: var(--brand-teal);
    letter-spacing: 0.5px;
  }
  .person__title {
    margin: 2px 0 0;
    font-size: 17px;
    color: var(--ink);
  }
  .company {
    margin-top: 58px;
    font-size: 17px;
    line-height: 1.3;
  }
  .company__name { color: var(--brand-green); font-weight: 700; }
  .contacts {
    list-style: none;
    margin: 18px 0 0;
    padding: 0;
    font-size: 17px;
    line-height: 1.45;
  }
  .contacts li { display: flex; align-items: center; gap: 8px; }
  .contacts svg { width: 18px; height: 18px; flex: none; }
  .card--back .wordmark {
    position: absolute;
    right: 60px;
    top: 150px;
    font-size: 72px;
    color: var(--brand-teal);
  }
  .card--back .wordmark__dot { width: 24px; height: 24px; background: var(--brand-green); }
  .hashtag {
    position: absolute;
    right: 96px;
    bottom: 40px;
    font-size: 19px;
    letter-spacing: 0.5px;
  }
</style>
</head>
<body>
<main class="sheet">
  <section class="card card--front" aria-label="Business card front">
    <div class="wordmark"><span>KAJU</span><span class="wordmark__dot"></span></div>
    <div class="front-url">www.kajufreightco.example</div>
  </section>

  <section class="card card--back" aria-label="Business card back">
    <h1 class="person__name">DANIEL REYES</h1>
    <p class="person__title">Managing Director</p>

    <div class="company">
      <div class="company__name">KAJU Freightways</div>
      <div>421, Address line here</div>
      <div>Country Name, 45452</div>
    </div>

    <ul class="contacts">
      <li>
        <svg viewBox="0 0 20 20" aria-hidden="true"><circle cx="10" cy="10" r="9" fill="none" stroke="var(--brand-green)" stroke-width="2"/><path d="M6.5 6c.6-.6 1.3-.6 1.7 0l.9 1.3c.3.5.2 1-.2 1.3l-.5.4c.5 1.1 1.5 2.1 2.6 2.6l.4-.5c.3-.4.8-.5 1.3-.2l1.3.9c.6.4.6 1.1 0 1.7-1.4 1.4-4.1.4-6-1.5S5.1 7.4 6.5 6z" fill="var(--brand-teal)"/></svg>
        044-555 018 274
      </li>
      <li>
        <svg viewBox="0 0 20 20" aria-hidden="true"><circle cx="10" cy="10" r="9" fill="none" stroke="var(--brand-green)" stroke-width="2"/><rect x="5.5" y="6.8" width="9" height="6.4" fill="var(--brand-teal)"/><path d="M5.5 6.8l4.5 3.6 4.5-3.6" fill="none" stroke="#fff" stroke-width="1"/></svg>
        hello@kajufreight.example
      </li>
      <li>
        <svg viewBox="0 0 20 20" aria-hidden="true"><circle cx="10" cy="10" r="9" fill="none" stroke="var(--brand-green)" stroke-width="2"/><circle cx="10" cy="10" r="5" fill="var(--brand-teal)"/><path d="M5 10h10M10 5c-2 2.8-2 7.2 0 10M10 5c2 2.8 2 7.2 0 10" fill="none" stroke="#fff" stroke-width="0.8"/></svg>
        www.kajufreightco.example
      </li>
    </ul>

    <div class="wordmark"><span>KAJU</span><span class="wordmark__dot"></span></div>
    <div class="hashtag">#ALLKAJU</div>
  </section>
</main>
</body>
</html>
```